Business Cards Design for the electrical wholesaler: clean bold dynamic :)

We need a business card design that would follow our latest brand guidelines. As an electrical wholesaler we want to bring a fresh look and feel into the industry. The design should be clean bold and dynamic. It should come alive with the renewed energy of our green colour. Our grey colour should keep things balanced and complement the notion of maturity and responsibility. We employ Lato as a corporate font however are not bound by this font and we’re open to interpretation here.

Target Market(s)

Electrical contractors

Industry/Entity Type

Business

Contact Information for Business Card

Logo
Name & Surname: Halyna Dorosh
Job Title: Director of Marketing
Email: halya.dorosh@quillmail.example
Cell phone: XXX.XXX.XXXX
Address: 20517 - 87 Ave. Edmonton, AB, Canada. T6K 4N8
Business Phone: 780.555.0184
Website: www.brovix.example

Font styles to use
Other font styles liked:
• Lato

Requirements
Must have
• Logo & website
Nice to have
• Brand elements - some of them you may find in the attached Brand Guidelines (e.g. three lines on the background signifying "W")

```html
<!DOCTYPE html>
<html lang="en">
<head>
<meta charset="utf-8">
<title>Brovix business cards</title>
<link rel="stylesheet" href="https://fonts.googleapis.com/css2?family=Roboto:wght@400;500&display=swap">
<style>
  :root {
    --backdrop: #ababab;
    --charcoal: #404346;
    --paper: #f1f1f1;
    --green: #7cc142;
    --ink: #4a4c4e;
    --white: #ffffff;
  }
  * { margin: 0; padding: 0; box-sizing: border-box; }
  html, body {
    width: 1200px; height: 576px; overflow: hidden;
    background: var(--backdrop);
    font-family: "Roboto", Arial, sans-serif;
  }
  .canvas { position: relative; width: 1200px; height: 576px; }
  .card { position: absolute; border-radius: 14px; overflow: hidden; }
  .card--front { left: 82px; top: 138px; width: 484px; height: 294px; background: var(--charcoal); }
  .card--back { left: 602px; top: 138px; width: 481px; height: 292px; background: var(--paper); }

  .wordmark { position: absolute; display: flex; align-items: center; gap: 10px; }
  .wordmark__mark { width: 26px; height: 26px; border-radius: 4px; background: var(--green); }
  .wordmark__name { font-weight: 500; line-height: 1; letter-spacing: 0.5px; }
  .card--front .wordmark { left: 50%; top: 146px; transform: translate(-50%, -50%); }
  .card--front .wordmark__name { font-size: 46px; color: var(--white); }
  .card--back .wordmark { right: 20px; top: 50px; }
  .card--back .wordmark__mark { width: 20px; height: 20px; border-radius: 3px; }
  .card--back .wordmark__name { font-size: 36px; color: var(--ink); }

  .person { position: absolute; left: 30px; top: 152px; }
  .person__name { font-size: 21px; font-weight: 500; color: var(--green); line-height: 1.1; }
  .person__title { font-size: 12.5px; color: var(--ink); margin-top: 4px; }

  .contact { position: absolute; left: 30px; top: 214px; font-size: 12.8px; color: var(--ink); line-height: 17px; white-space: nowrap; }
  .contact__row { display: flex; align-items: center; gap: 8px; }
  .contact__item { display: flex; align-items: center; gap: 7px; }
  .contact__icon { width: 13px; height: 13px; flex: none; }
  .contact__address { margin-top: 3px; }
</style>
</head>
<body>
<main class="canvas">
  <section class="card card--front" aria-label="Card front">
    <div class="wordmark">
      <span class="wordmark__mark"></span>
      <span class="wordmark__name">brovix</span>
    </div>
  </section>

  <section class="card card--back" aria-label="Card back">
    <div class="wordmark">
      <span class="wordmark__mark"></span>
      <span class="wordmark__name">brovix</span>
    </div>

    <div class="person">
      <h1 class="person__name">Halyna Dorosh</h1>
      <p class="person__title">Director of Marketing</p>
    </div>

    <div class="contact">
      <div class="contact__row">
        <span class="contact__item">
          <svg class="contact__icon" viewBox="0 0 16 16" aria-hidden="true">
            <circle cx="8" cy="8" r="8" fill="var(--green)"/>
            <path d="M5.2 4.2l1.5 0 .7 1.9-1 .7a5 5 0 0 0 2.8 2.8l.7-1 1.9.7 0 1.5c-3.8.3-6.9-2.8-6.6-6.6z" fill="var(--white)"/>
          </svg>
          +1 780-555-0184
        </span>
      </div>
      <div class="contact__row">
        <span class="contact__item">
          <svg class="contact__icon" viewBox="0 0 16 16" aria-hidden="true">
            <circle cx="8" cy="8" r="8" fill="var(--green)"/>
            <rect x="4" y="5.2" width="8" height="5.6" rx="0.6" fill="var(--white)"/>
            <path d="M4.3 5.6L8 8.4l3.7-2.8" fill="none" stroke="var(--green)" stroke-width="0.9"/>
          </svg>
          halya.dorosh@quillmail.example
        </span>
        <span class="contact__item">
          <svg class="contact__icon" viewBox="0 0 16 16" aria-hidden="true">
            <circle cx="8" cy="8" r="8" fill="var(--green)"/>
            <g fill="none" stroke="var(--white)" stroke-width="0.9">
              <circle cx="8" cy="8" r="4"/>
              <ellipse cx="8" cy="8" rx="1.7" ry="4"/>
              <path d="M4 8h8"/>
            </g>
          </svg>
          www.brovix.example
        </span>
      </div>
      <p class="contact__address">20517 - 87 Ave. Edmonton, AB, Canada T6K 4N8</p>
    </div>
  </section>
</main>
</body>
</html>
```